Corporate Travel Technology Company needs new Business Card design

We need a new business card design to reflect our re-branded company. Our company is called tolvEn (pronounced tolvenn) and we provide Business Intelligence and mobile travel management solutions for the corporate travel industry. Our multinational customers use our solutions to manage large travel budgets and frequent travellers, as well as to save money and reduce risk. We'd like to see designs that use the blue and green palette as well as our corporate logo (attached below). The design should communicate innovation, insight, forward thinking, contemporary, trusted.

Target Market(s)

Large multinational corporates and Travel Agencies.

Industry/Entity Type

Business

Contact Information for Business Card

Rosalind Mercer
Chief Executive
tolvEn
Phone number - +61 (0)2 8134 2907
Email address - rosalind.mercer@tolven-example.com
Mobile number - +61 (0)438 516 702
www.tolven-example.com

Font styles to use
Other font styles liked:
• Please use font as close to corporate logo as possible

Colors
0255a3
0393ce
00a990
33b8a4
33a6d7
3176b5

Requirements
Must have
• Please include the words;
• Mobile Travel Management
• Accelerating Travel Business Insights
• Use corporate logo - although icon can be stylised if needed

```html
<!DOCTYPE html>
<html lang="en">
<head>
<meta charset="utf-8">
<title>tolvEn business card</title>
<link rel="stylesheet" href="https://fonts.googleapis.com/css2?family=Open+Sans:wght@300;400;600&display=swap">
<style>
  :root {
    --page: #eceff1;
    --paper: #f7f8f8;
    --sky: #36c4e8;
    --sky-deep: #1fa6d6;
    --ink: #141b1f;
    --ink-soft: #2c3438;
    --brand: #2aa9d8;
    --green: #00a990;
    --green-soft: #33b8a4;
    --white: #ffffff;
  }
  * { box-sizing: border-box; margin: 0; padding: 0; }
  html, body { width: 1200px; height: 892px; overflow: hidden; }
  body {
    background: var(--page);
    font-family: "Open Sans", Arial, sans-serif;
    display: flex;
    flex-direction: column;
    align-items: center;
    justify-content: center;
    gap: 30px;
  }
  .card {
    position: relative;
    width: 700px;
    height: 400px;
    overflow: hidden;
    box-shadow: 0 6px 18px rgba(0,0,0,0.18);
  }
  .card-front { background: var(--paper); }
  .card-front .wave { position: absolute; inset: 0; }
  .brand-name { font-weight: 400; letter-spacing: 1px; line-height: 1; }
  .brand-dot { border-radius: 50%; flex: none; }

  .card-front .brand-block { position: absolute; left: 48px; top: 112px; }
  .card-front .brand { display: flex; align-items: center; gap: 14px; }
  .card-front .brand-dot { width: 34px; height: 34px; background: var(--green); }
  .card-front .brand-name { font-size: 62px; color: var(--brand); }
  .card-front .tagline {
    margin-top: 10px;
    font-size: 14px;
    font-weight: 600;
    letter-spacing: 0.5px;
    color: var(--green);
  }

  .contact {
    position: absolute;
    right: 30px;
    top: 172px;
    text-align: right;
    color: var(--ink);
  }
  .contact-name { font-size: 30px; font-weight: 400; line-height: 1.1; }
  .contact-role { font-size: 17px; font-weight: 300; color: var(--ink-soft); margin-bottom: 14px; }
  .contact-list { list-style: none; }
  .contact-list li {
    display: flex;
    justify-content: flex-end;
    align-items: center;
    gap: 12px;
    font-size: 17px;
    font-weight: 400;
    line-height: 27px;
  }
  .contact-icon { width: 16px; height: 16px; flex: none; }

  .card-back {
    background: radial-gradient(ellipse at 40% 45%, var(--sky) 0%, var(--sky-deep) 100%);
    display: flex;
    flex-direction: column;
    align-items: center;
    justify-content: center;
    gap: 18px;
  }
  .card-back .brand { display: flex; align-items: center; gap: 22px; }
  .card-back .brand-dot { width: 62px; height: 62px; background: var(--white); }
  .card-back .brand-name { font-size: 110px; font-weight: 300; color: var(--white); }
  .card-back .rule { width: 120px; height: 4px; background: var(--green-soft); }
  .card-back .tagline {
    font-size: 20px;
    font-weight: 400;
    letter-spacing: 1px;
    color: var(--white);
  }
</style>
</head>
<body>
  <section class="card card-front" aria-label="Business card front">
    <svg class="wave" viewBox="0 0 700 400" aria-hidden="true">
      <path d="M0,300 C190,300 250,250 320,170 C390,90 470,40 700,38 L700,400 L0,400 Z" fill="var(--sky)"/>
      <path d="M0,322 C200,322 265,272 335,190 C405,108 480,62 700,60" fill="none" stroke="#ffffff" stroke-width="5"/>
    </svg>
    <div class="brand-block">
      <div class="brand">
        <span class="brand-dot"></span>
        <span class="brand-name">tolvEn</span>
      </div>
      <p class="tagline">Mobile Travel Management</p>
    </div>
    <div class="contact">
      <p class="contact-name">Rosalind Mercer</p>
      <p class="contact-role">Chief Executive</p>
      <ul class="contact-list">
        <li>+61 (0)438 516 702
          <svg class="contact-icon" viewBox="0 0 16 16" aria-hidden="true"><rect width="16" height="16" fill="var(--ink)"/><rect x="5" y="2.5" width="6" height="11" rx="1" fill="none" stroke="#fff" stroke-width="1.4"/></svg></li>
        <li>+61 (0)2 8134 2907
          <svg class="contact-icon" viewBox="0 0 16 16" aria-hidden="true"><rect width="16" height="16" fill="var(--ink)"/><path d="M4,4 C4,9 7,12 12,12 L12,10 L10,9 L9,10 C7.5,9.5 6.5,8.5 6,7 L7,6 L6,4 Z" fill="#fff"/></svg></li>
        <li>rosalind.mercer@tolven-example.com
          <svg class="contact-icon" viewBox="0 0 16 16" aria-hidden="true"><rect width="16" height="16" fill="var(--ink)"/><rect x="3" y="4.5" width="10" height="7" fill="none" stroke="#fff" stroke-width="1.3"/><path d="M3,4.5 L8,8.5 L13,4.5" fill="none" stroke="#fff" stroke-width="1.3"/></svg></li>
        <li>www.tolven-example.com
          <svg class="contact-icon" viewBox="0 0 16 16" aria-hidden="true"><rect width="16" height="16" fill="var(--ink)"/><circle cx="8" cy="8" r="5" fill="none" stroke="#fff" stroke-width="1.3"/><path d="M3,8 H13 M8,3 C5.5,6 5.5,10 8,13 M8,3 C10.5,6 10.5,10 8,13" fill="none" stroke="#fff" stroke-width="1"/></svg></li>
      </ul>
    </div>
  </section>

  <section class="card card-back" aria-label="Business card back">
    <div class="brand">
      <span class="brand-dot"></span>
      <span class="brand-name">tolvEn</span>
    </div>
    <span class="rule"></span>
    <p class="tagline">Accelerating Travel Business Insights</p>
  </section>
</body>
</html>
```